Building company buisness cards

We are looking for a sharp modern new look for our business cards.
We are a New Zealand based company that specialises in house and land packages.
We have attached a photo of the current logo and would like to see if it can be improved somehow if needed.
We are open to any colours but we have chosen green at this stage.
Feel free to change the font and make the logo smarter looking.
Play with the colours and see what looks best.

We want a card that looks so good know one will want to throw it away!

Target Market(s)

Home buyers

Industry/Entity Type

Building

Contact Information for Business Card

Derek Tolvane
0217394062
dtolvane@quillmarkhomesteads.co.nz
quillmarkhomesteads.co.nz

Font styles to use
Serif
Sans Serif

Colors

Designer to choose colors to be used in the design.

Requirements
Must have
• Logo and company name on one side, details on the other side
Nice to have
• Color codes for the original green are HEX #4a8028, RGB(74,128,40), CMYK(42,0,69,50)
• Round corners, Raised and/or spot UV

```html
<!DOCTYPE html>
<html lang="en">
<head>
<meta charset="utf-8">
<title>Quillmark Homesteads – Business Card</title>
<link href="https://fonts.googleapis.com/css2?family=Nunito:wght@800&family=Open+Sans:wght@300;400&display=swap" rel="stylesheet">
<style>
  :root {
    --page-bg: #e9e6e1;
    --card-white: #fbfbfa;
    --card-black: #0d0d0d;
    --brand-green: #1fae2c;
    --text-light: #f2f2f2;
    --photo-sky: #e4e7ea;
    --photo-siding: #8b8f94;
    --photo-stone: #7d6f5e;
  }
  html, body {
    margin: 0;
    width: 1200px;
    height: 1024px;
    overflow: hidden;
    background: var(--page-bg);
  }
  .card {
    position: absolute;
    left: 100px;
    top: 226px;
    width: 1000px;
    height: 572px;
    border-radius: 14px;
    overflow: hidden;
    box-shadow: 0 8px 26px rgba(0,0,0,0.18);
  }
  .card-shapes {
    position: absolute;
    inset: 0;
  }
  .brand {
    position: absolute;
    left: 120px;
    top: 96px;
    display: flex;
    align-items: flex-start;
    gap: 18px;
  }
  .brand-square {
    width: 40px;
    height: 40px;
    margin-top: 10px;
    background: var(--brand-green);
  }
  .brand-name {
    margin: 0;
    font-family: "Nunito", sans-serif;
    font-weight: 800;
    font-size: 54px;
    line-height: 0.98;
    color: var(--brand-green);
    letter-spacing: -0.5px;
  }
  .brand-rule {
    position: absolute;
    left: 178px;
    top: 236px;
    width: 150px;
    height: 1px;
    background: #c9c9c9;
  }
  .details {
    position: absolute;
    left: 600px;
    top: 0;
    width: 400px;
    height: 572px;
    box-sizing: border-box;
    padding: 30px 40px 0 30px;
    text-align: right;
    font-family: "Open Sans", sans-serif;
    color: var(--text-light);
  }
  .contact-icons {
    display: flex;
    justify-content: flex-end;
    gap: 12px;
    margin-bottom: 22px;
  }
  .contact-icons span {
    display: block;
    width: 18px;
    height: 18px;
    background: var(--brand-green);
  }
  .contact-name {
    margin: 0 0 56px;
    font-weight: 400;
    font-size: 34px;
    line-height: 1.2;
    color: var(--brand-green);
    white-space: nowrap;
  }
  .contact-list {
    list-style: none;
    margin: 0;
    padding: 0;
    font-weight: 300;
    font-size: 17px;
    line-height: 2;
    white-space: nowrap;
  }
</style>
</head>
<body>
  <div class="card">
    <svg class="card-shapes" viewBox="0 0 1000 572" width="1000" height="572">
      <defs>
        <linearGradient id="houseTones" x1="0" y1="0" x2="1" y2="1">
          <stop offset="0" stop-color="var(--photo-sky)"/>
          <stop offset="0.5" stop-color="var(--photo-siding)"/>
          <stop offset="1" stop-color="var(--photo-stone)"/>
        </linearGradient>
      </defs>
      <rect class="photo-panel" role="img" aria-label="Photo of a grey weatherboard house with white-framed windows and stone cladding" x="0" y="0" width="600" height="572" fill="url(#houseTones)"/>
      <polygon class="logo-panel" points="0,0 600,0 600,330 300,392 0,330" fill="var(--card-white)"/>
      <polyline class="panel-edge" points="0,330 300,392 600,330" fill="none" stroke="#1a1a1a" stroke-width="5"/>
      <rect class="details-panel" x="600" y="0" width="400" height="572" fill="var(--card-black)"/>
    </svg>

    <div class="brand">
      <div class="brand-square"></div>
      <h1 class="brand-name">quillmark<br>homesteads.</h1>
    </div>
    <div class="brand-rule"></div>

    <div class="details">
      <div class="contact-icons"><span></span><span></span><span></span></div>
      <h2 class="contact-name">Derek Tolvane</h2>
      <ul class="contact-list">
        <li>0217394062</li>
        <li>dtolvane@quillmarkhomesteads.co.nz</li>
        <li>quillmarkhomesteads.co.nz</li>
      </ul>
    </div>
  </div>
</body>
</html>
```